Harbor Ledger Funds Bus card and Logo

I need a logo design and Bus card design. The fund focuses on evaluating and investing in minerals (sub-surface rights) and real estate.

Harbor ledger refers to a book of knowledge that each plebe gets when entering the Kelmont Marine Academy (my alma mater)

Target Market(s)

Investors and financial advisors

Contact Information for Business Card

Simple - perhaps a logo with a theme on book of knowledge

Logo Text

Ex Scientia Imperium

Font styles to use
Serif
Sans Serif

Colors

Designer to choose colors to be used in the design.

Requirements
Must have
• memorable logo that is relatively simple

```html
<!DOCTYPE html>
<html lang="en">
<head>
<meta charset="utf-8">
<title>Harbor Ledger Funds – Business Card</title>
<link href="https://fonts.googleapis.com/css2?family=Cinzel:wght@500&family=Questrial&display=swap" rel="stylesheet">
<style>
  :root {
    --backdrop: #26272b;
    --card: #1e2124;
    --card-edge: #2a2d31;
    --gloss: #54585e;
    --ink: #f2f3f4;
    --accent: #2ea6df;
    --muted: #c9ccd0;
  }
  html, body {
    margin: 0;
    padding: 0;
    width: 1200px;
    height: 800px;
    overflow: hidden;
    background: var(--backdrop);
  }
  .canvas {
    position: relative;
    width: 1200px;
    height: 800px;
  }
  .card {
    position: absolute;
    width: 525px;
    height: 300px;
    border-radius: 18px;
    background: var(--card);
    box-shadow: 0 18px 40px rgba(0,0,0,.45), inset 0 0 0 1px var(--card-edge);
    overflow: hidden;
  }
  .card--front { left: 70px; top: 70px; }
  .card--back { left: 605px; top: 430px; }

  .wordmark {
    position: absolute;
    font-family: "Cinzel", serif;
    font-weight: 500;
    text-align: center;
    letter-spacing: 2px;
    line-height: 1.1;
  }
  .wordmark__dot {
    display: block;
    width: 14px;
    height: 14px;
    border-radius: 50%;
    margin: 0 auto 14px;
  }
  .wordmark__main { display: block; font-size: 34px; }
  .wordmark__sub {
    display: block;
    font-size: 15px;
    letter-spacing: 6px;
    margin-top: 6px;
  }

  .card--front .wordmark {
    left: 0; right: 0; top: 100px;
    color: var(--gloss);
  }
  .card--front .wordmark__dot { background: var(--gloss); }

  .card--back .wordmark {
    left: 20px; width: 250px; top: 110px;
    color: var(--ink);
  }
  .card--back .wordmark__main { font-size: 26px; }
  .card--back .wordmark__sub { font-size: 12px; letter-spacing: 5px; }
  .card--back .wordmark__dot { background: var(--accent); }

  .divider {
    position: absolute;
    left: 288px; top: 70px;
    width: 1px; height: 160px;
    background: var(--accent);
  }
  .contact {
    position: absolute;
    left: 310px; top: 78px;
    font-family: "Questrial", sans-serif;
    color: var(--ink);
  }
  .contact__name {
    margin: 0;
    font-size: 16px;
    font-weight: 700;
    letter-spacing: .5px;
  }
  .contact__role {
    margin: 2px 0 16px;
    font-size: 12px;
    color: var(--accent);
  }
  .contact__list {
    list-style: none;
    margin: 0;
    padding: 0;
    font-size: 12.5px;
    line-height: 1.55;
    color: var(--muted);
  }
  .contact__item { display: flex; align-items: center; gap: 7px; }
  .contact__item--plain { padding-left: 0; }
  .contact__icon { width: 11px; height: 11px; flex: none; }
</style>
</head>
<body>
<main class="canvas">

  <section class="card card--front" aria-label="Business card front">
    <div class="wordmark">
      <span class="wordmark__dot"></span>
      <span class="wordmark__main">HARBOR LEDGER</span>
      <span class="wordmark__sub">FUNDS LLC</span>
    </div>
  </section>

  <section class="card card--back" aria-label="Business card back">
    <div class="wordmark">
      <span class="wordmark__dot"></span>
      <span class="wordmark__main">HARBOR LEDGER</span>
      <span class="wordmark__sub">FUNDS LLC</span>
    </div>

    <div class="divider"></div>

    <div class="contact">
      <p class="contact__name">DANIEL MORROW</p>
      <p class="contact__role">President</p>
      <ul class="contact__list">
        <li class="contact__item contact__item--plain">PO BOX 418, Bayline Road</li>
        <li class="contact__item contact__item--plain">Port Carrow</li>
        <li class="contact__item">
          <svg class="contact__icon" viewBox="0 0 11 11"><rect x="1" y="1" width="9" height="9" fill="none" stroke="#2ea6df" stroke-width="1.5"/></svg>
          555 014 2287
        </li>
        <li class="contact__item">
          <svg class="contact__icon" viewBox="0 0 11 11"><rect x="0.5" y="2" width="10" height="7" fill="#2ea6df"/><path d="M0.5 2 L5.5 6 L10.5 2" fill="none" stroke="#1e2124" stroke-width="1"/></svg>
          info@harborledger.com
        </li>
      </ul>
    </div>
  </section>

</main>
</body>
</html>
```